Moxy Fen needs some awesome stationary

Do you have what it takes to get my brand? You either do or you don't, have a crack at a design and you my just win my business.

I don't want to waste your or my time, so put your creative genius on either a business card or envelope.

I however need a package of stationary that follows the same brand. I will message you to complete the remaining should I like your first submission.

Here is what I need, have a go!

Basically I need the following for my small business based in melbourne.
- Letterhead (printer ready and MS Word)
- Business Card
- Compliments Slip
- Envelope
- Proposal Cover Page (MS Word only)
- Presentation Folder
- Marbled Fox Cards
- Student Name Tent
- Index Cards
- Vell-Ka

I am establishing the brand and it must be modern, professional but also relaxed; that is not formal and not corporate. It represents a company are leaders, but small enough to care and operate like a bunch of friends. We are bringing people and conversations back to business, and turfing out all the bureaucracy and crazy and wasteful procedures. Its about "lets talk and figure it out together and find even better ways".

Target Market(s)

Mainly companies that build software products, but Agile practices are used in many other industries (even graphic design projects)

Industry/Entity Type

Information Technology

Font styles to use
Sans Serif

Colors
3176b5
aaaaaa

Requirements
Must have
• I like curves and circles and not boxes or rectangles.
• I want a colour rich design with my brand colours, but it must be balanced.
• I want more modern than traditional, but simple modern
Should not have
• Not corporate
• Please don't waste my time if your not going to think about it.
• Don't mess with my primary logo
• Don't change my colours
• Don't overlay logo on image

```html
<!DOCTYPE html>
<html lang="en">
<head>
<meta charset="utf-8">
<title>Moxy Fen – Index Cards</title>
<link rel="stylesheet" href="https://fonts.googleapis.com/css2?family=Fira+Sans:wght@500&family=Fjalla+One&display=swap">
<style>
  :root {
    --backdrop: #3a9fda;
    --card-white: #ffffff;
    --rule: #e6e6e6;
    --navy: #2e3192;
    --brand-blue: #1f4f9c;
    --red: #ed1c24;
    --magenta: #ec008c;
    --indigo: #2e3192;
    --yellow: #fff200;
    --green: #00a651;
  }
  * { box-sizing: border-box; margin: 0; padding: 0; }
  html, body {
    width: 1200px; height: 960px; overflow: hidden;
    background: var(--backdrop);
  }
  .sheet { position: relative; width: 1200px; height: 960px; }

  .index-card {
    position: absolute;
    display: flex; flex-direction: column;
    background: var(--card-white);
    box-shadow: 7px 7px 8px rgba(0, 0, 0, 0.28);
  }
  .index-card--top { width: 356px; height: 422px; }
  .index-card--bottom { width: 362px; height: 432px; }

  .index-card .header-band { height: 14.3%; background: var(--accent); }
  .index-card .writing-area { flex: 1; display: flex; flex-direction: column; }
  .index-card .writing-line { flex: 1; border-bottom: 1px solid var(--rule); }
  .index-card .writing-line:last-child { border-bottom: 2px solid var(--navy); }

  .index-card .footer {
    position: relative; height: 68px;
    border-bottom: 3px solid var(--accent);
  }
  .brand-mark {
    position: absolute; left: 12px; top: 26px;
    display: flex; flex-direction: column; align-items: center; gap: 3px;
  }
  .brand-mark .brand-dot {
    width: 26px; height: 26px; border-radius: 50%;
    background: var(--brand-blue);
  }
  .brand-mark .brand-name {
    font-family: "Fira Sans", sans-serif; font-weight: 500;
    font-size: 9px; color: var(--brand-blue); white-space: nowrap;
  }
  .company-name {
    position: absolute; left: 0; right: 0; bottom: 6px;
    text-align: center;
    font-family: "Fjalla One", sans-serif; font-size: 9.5px;
    color: var(--brand-blue); letter-spacing: 0.2px;
  }
  .stamp-circle {
    position: absolute; right: 9px; top: 5px;
    width: 62px; height: 62px;
  }

  .card-red { --accent: var(--red); left: 37px; top: 32px; }
  .card-magenta { --accent: var(--magenta); left: 420px; top: 32px; width: 354px; }
  .card-indigo { --accent: var(--indigo); left: 811px; top: 32px; width: 358px; height: 424px; }
  .card-yellow { --accent: var(--yellow); left: 171px; top: 502px; }
  .card-green { --accent: var(--green); left: 667px; top: 502px; }
</style>
</head>
<body>
<main class="sheet">

  <section class="index-card index-card--top card-red">
    <div class="header-band"></div>
    <div class="writing-area">
      <div class="writing-line"></div><div class="writing-line"></div><div class="writing-line"></div>
      <div class="writing-line"></div><div class="writing-line"></div><div class="writing-line"></div>
      <div class="writing-line"></div>
    </div>
    <div class="footer">
      <div class="brand-mark"><span class="brand-dot"></span><span class="brand-name">Moxy Fen</span></div>
      <p class="company-name">Moxy Fen Pty Ltd</p>
      <svg class="stamp-circle" viewBox="0 0 62 62"><circle cx="31" cy="31" r="30" fill="none" stroke="#1f4f9c" stroke-width="1.6"/></svg>
    </div>
  </section>

  <section class="index-card index-card--top card-magenta">
    <div class="header-band"></div>
    <div class="writing-area">
      <div class="writing-line"></div><div class="writing-line"></div><div class="writing-line"></div>
      <div class="writing-line"></div><div class="writing-line"></div><div class="writing-line"></div>
      <div class="writing-line"></div>
    </div>
    <div class="footer">
      <div class="brand-mark"><span class="brand-dot"></span><span class="brand-name">Moxy Fen</span></div>
      <p class="company-name">Moxy Fen Pty Ltd</p>
      <svg class="stamp-circle" viewBox="0 0 62 62"><circle cx="31" cy="31" r="30" fill="none" stroke="#1f4f9c" stroke-width="1.6"/></svg>
    </div>
  </section>

  <section class="index-card index-card--top card-indigo">
    <div class="header-band"></div>
    <div class="writing-area">
      <div class="writing-line"></div><div class="writing-line"></div><div class="writing-line"></div>
      <div class="writing-line"></div><div class="writing-line"></div><div class="writing-line"></div>
      <div class="writing-line"></div>
    </div>
    <div class="footer">
      <div class="brand-mark"><span class="brand-dot"></span><span class="brand-name">Moxy Fen</span></div>
      <p class="company-name">Moxy Fen Pty Ltd</p>
      <svg class="stamp-circle" viewBox="0 0 62 62"><circle cx="31" cy="31" r="30" fill="none" stroke="#1f4f9c" stroke-width="1.6"/></svg>
    </div>
  </section>

  <section class="index-card index-card--bottom card-yellow">
    <div class="header-band"></div>
    <div class="writing-area">
      <div class="writing-line"></div><div class="writing-line"></div><div class="writing-line"></div>
      <div class="writing-line"></div><div class="writing-line"></div><div class="writing-line"></div>
      <div class="writing-line"></div>
    </div>
    <div class="footer">
      <div class="brand-mark"><span class="brand-dot"></span><span class="brand-name">Moxy Fen</span></div>
      <p class="company-name">Moxy Fen Pty Ltd</p>
      <svg class="stamp-circle" viewBox="0 0 62 62"><circle cx="31" cy="31" r="30" fill="none" stroke="#1f4f9c" stroke-width="1.6"/></svg>
    </div>
  </section>

  <section class="index-card index-card--bottom card-green">
    <div class="header-band"></div>
    <div class="writing-area">
      <div class="writing-line"></div><div class="writing-line"></div><div class="writing-line"></div>
      <div class="writing-line"></div><div class="writing-line"></div><div class="writing-line"></div>
      <div class="writing-line"></div>
    </div>
    <div class="footer">
      <div class="brand-mark"><span class="brand-dot"></span><span class="brand-name">Moxy Fen</span></div>
      <p class="company-name">Moxy Fen Pty Ltd</p>
      <svg class="stamp-circle" viewBox="0 0 62 62"><circle cx="31" cy="31" r="30" fill="none" stroke="#1f4f9c" stroke-width="1.6"/></svg>
    </div>
  </section>

</main>
</body>
</html>
```